Printer Cartridges Supplier Namecard

Attached is my company logo and the design of my current namecard. I would like to have a more special look for it. Can have a little cuteness too rather than those normal standard feel. I'm a supplier mainly dealing with original and compatible printer toner cartridges, some other products like paper supplies as well.

Target Market(s)

Companies, businesses, corporates

Industry/Entity Type

It Company

Contact Information for Business Card

Logo, name, contact, address, supplies and maybe a slogan

Colors
85cae6
33a6d7
3176b5
0255a3
0792cd
85abd2

Requirements
Must have
• Logo, name, contact and address basic details.
• Must include some pictures, not just rearrange what I'm currently having.
Nice to have
• Be creative and bold, a diiferent traditional feel.

```html
<!DOCTYPE html>
<html lang="en">
<head>
<meta charset="utf-8">
<title>tonerbay.sg Namecard</title>
<link href="https://fonts.googleapis.com/css2?family=Lato:wght@400;700&display=swap" rel="stylesheet">
<style>
  :root {
    --stage: #2e2e2e;
    --card-light: #ffffff;
    --card-dark: #58595b;
    --brand-blue: #5eb3e4;
    --text-dark: #222222;
    --text-grey: #58595b;
    --rule: #555555;
    --white: #ffffff;
  }
  * { margin: 0; padding: 0; box-sizing: border-box; }
  html, body { width: 1200px; height: 900px; overflow: hidden; }
  body {
    background: var(--stage);
    font-family: 'Lato', sans-serif;
    position: relative;
  }
  .card {
    position: absolute;
    top: 170px;
    width: 347px;
    height: 561px;
    box-shadow: 3px 4px 6px rgba(0,0,0,0.45);
  }
  .card--front { left: 259px; background: var(--card-light); }
  .card--back { left: 631px; background: var(--card-dark); }

  .brand {
    position: absolute;
    left: 0; right: 0;
    display: flex;
    align-items: center;
    justify-content: center;
    gap: 12px;
  }
  .brand__mark {
    width: 40px; height: 40px;
    background: var(--brand-blue);
    border-radius: 6px;
  }
  .brand__name {
    font-weight: 400;
    font-size: 48px;
    letter-spacing: 0.5px;
  }
  .card--front .brand { top: 108px; }
  .card--front .brand__name { color: var(--text-grey); }
  .card--back .brand { top: 174px; }
  .card--back .brand__name { color: var(--white); }
  .tagline {
    position: absolute;
    top: 238px; left: 0; right: 0;
    text-align: center;
    color: var(--white);
    font-size: 10.5px;
    font-style: italic;
  }

  .contact {
    position: absolute;
    top: 252px; left: 0; right: 0;
    text-align: center;
    color: var(--text-dark);
  }
  .contact__name { color: var(--brand-blue); font-size: 27px; line-height: 32px; }
  .contact__role { font-size: 16px; line-height: 20px; }
  .contact__rule { width: 128px; height: 1px; background: var(--rule); margin: 6px auto 6px; }
  .contact__line { font-size: 16px; line-height: 21px; }
  .contact__label, .contact__web { color: var(--brand-blue); }
  .contact__address { font-size: 16px; line-height: 21px; margin-top: 8px; }

  .product-strip {
    position: absolute;
    left: 2px; right: 4px;
    top: 440px; height: 95px;
    background: linear-gradient(90deg, #e6eef5 0%, #cfd6dc 45%, #eef1f3 70%, #dfe7ee 100%);
  }

  .services {
    position: absolute;
    left: 0; right: 0;
    top: 388px; height: 125px;
    background: var(--brand-blue);
    color: var(--white);
    text-align: center;
    font-size: 16.5px;
    line-height: 21.5px;
    padding-top: 18px;
  }
</style>
</head>
<body>
  <section class="card card--front">
    <div class="brand">
      <span class="brand__mark"></span>
      <span class="brand__name">tonerbay.sg</span>
    </div>
    <div class="contact">
      <p class="contact__name">Mira Tan</p>
      <p class="contact__role">Sales Executive</p>
      <div class="contact__rule"></div>
      <p class="contact__line"><span class="contact__label">M:</span> 9000 1234</p>
      <p class="contact__line"><span class="contact__label">E:</span> mira@tonerbay.sg</p>
      <p class="contact__line contact__web">www.tonerbay.sg</p>
      <div class="contact__rule"></div>
      <p class="contact__address">17A Harbourview Crescent<br>#05-112, Singapore 540017</p>
    </div>
    <div class="product-strip" role="img" aria-label="Row of products: paper reams, an office printer and four CMYK ink cartridges"></div>
  </section>

  <section class="card card--back">
    <div class="brand">
      <span class="brand__mark"></span>
      <span class="brand__name">tonerbay.sg</span>
    </div>
    <p class="tagline">Compatible printer ink and toner solutions</p>
    <div class="services">
      <p>Printer Ink &amp; Toner Cartridges</p>
      <p>Original Printer Cartridges</p>
      <p>Paper Products</p>
      <p>Printer Maintainence &amp; Repair</p>
    </div>
  </section>
</body>
</html>
```